Goodlooking website for a company who is working in the IT consultancy

We want a new website designed in WordPress. You can take www.vantoro.nl as an example. It should be a website with some short blocks of information about the company, nice pictures of our partners and our employees. A job page with a clear filter.

Target Market(s)

B2B

Industry/Entity Type

It Company

Coding

Coded - Design and coding required

Number of Pages Required

5+ page

Font styles to use
Sans Serif

Colors
0455a3
34a7d8

Requirements
Must have
• Check briefing

```html
<!DOCTYPE html>
<html lang="en">
<head>
<meta charset="utf-8">
<title>Orvane – Critical IT Systems</title>
<link href="https://fonts.googleapis.com/css2?family=Open+Sans:wght@400;600;700&display=swap" rel="stylesheet">
<style>
:root{
  --green:#1ba585;
  --teal-dark:#11343f;
  --slate:#2c3a45;
  --blue:#1a9acb;
  --grey-light:#f0f0f0;
  --grey-band:#e6e6e6;
  --footer:#1f2830;
  --text:#444;
  --footer-text:#b5bcc4;
  --white:#fff;
}
*{box-sizing:border-box;margin:0;padding:0}
html,body{width:671px;height:1200px;overflow:hidden}
body{position:relative;background:var(--white);font-family:"Open Sans",Arial,sans-serif;color:var(--text)}
.abs{position:absolute}

/* header */
.brand{left:74px;top:14px;display:flex;align-items:center;gap:9px}
.brand-mark{width:46px;height:46px;border-radius:50%;background:var(--teal-dark)}
.brand-name{font-size:21px;font-weight:600;color:var(--teal-dark);letter-spacing:3px;line-height:1}
.brand-tag{font-size:5.5px;color:var(--green);letter-spacing:1px;margin-top:3px;padding-left:14px}
.phone{right:74px;top:10px;font-size:14px;font-weight:600;color:#222;display:flex;align-items:center;gap:5px}
.nav{right:74px;top:49px;display:flex;gap:15px;font-size:7.5px;font-weight:600;color:#888}
.nav .active{color:var(--green)}

/* hero */
.hero{left:0;top:72px;width:671px;height:246px}
.hero-photo{position:absolute;inset:0;background:linear-gradient(120deg,#8c7f74,#c9c2b8 45%,#6b625c)}
.hero-title{left:74px;top:148px;font-size:23px;font-weight:600;color:var(--white);line-height:1.2}
.hero-btn{left:74px;top:212px;width:63px;height:25px;background:var(--slate);color:var(--white);font-size:7px;font-weight:700;display:flex;align-items:center;justify-content:center;border-radius:2px}

/* about */
.section-title{left:0;width:671px;text-align:center;font-weight:600}
.about-title{top:366px;font-size:19px;color:var(--green)}
.about-text{left:74px;top:393px;width:523px;text-align:center;font-size:6.6px;line-height:1.85;color:#555}

/* what we do */
.wwd-photo{left:0;top:494px;width:335px;height:296px;background:linear-gradient(135deg,#b9bfc3,#dfe2e3 50%,#8f9aa0)}
.wwd-title{left:76px;top:522px;font-size:35px;font-weight:600;color:var(--white)}
.wwd-side{left:600px;top:494px;width:71px;height:296px;background:var(--grey-band)}
.tile{width:128px;height:147px;padding:32px 9px 0;color:var(--white);font-size:12px;font-weight:600;line-height:1.4}
.tile-icon{height:40px;margin-bottom:14px;display:flex;align-items:flex-end}
.tile-green{background:var(--green);left:338px;top:494px}
.tile-teal{background:var(--teal-dark);left:469px;top:494px}
.tile-slate{background:var(--slate);left:338px;top:643px}
.tile-blue{background:var(--blue);left:469px;top:643px}

/* jobs */
.jobs-title{top:838px;font-size:19px;color:var(--blue)}
.job-card{top:874px;width:167px;height:107px;background:var(--grey-light);border-top:2px solid var(--blue);padding:13px 10px}
.job-date{font-size:7px;color:var(--blue)}
.job-text{font-size:8.6px;line-height:1.45;color:#444;margin-top:3px}
.job-btn{margin-top:8px;width:45px;height:19px;background:var(--slate);color:var(--white);font-size:6px;display:flex;align-items:center;justify-content:center}
.view-all{left:0;width:671px;top:992px;text-align:center;font-size:7px;color:#444}
.view-all span{text-decoration:underline}

/* partners */
.partners{left:0;top:1054px;width:671px;height:81px;background:var(--grey-band)}
.partners-label{left:73px;top:1083px;font-size:17.5px;font-weight:600;color:var(--white)}
.partner{top:1078px;height:32px}

/* footer */
.footer{left:0;top:1137px;width:671px;height:63px;background:var(--footer)}
.footer-links{left:74px;top:1157px;font-size:6.3px;color:var(--footer-text);word-spacing:2px}
.footer-copy{left:74px;top:1171px;font-size:6.3px;color:var(--footer-text)}
.social{top:1161px;width:14px;height:14px;border-radius:50%}
.footer-address{right:74px;top:1157px;font-size:6.3px;color:var(--footer-text);text-align:right;line-height:14px}
</style>
</head>
<body>

<header>
  <div class="abs brand">
    <div class="brand-mark"></div>
    <div>
      <div class="brand-name">ORVANE</div>
      <div class="brand-tag">CRITICAL IT SYSTEMS</div>
    </div>
  </div>
  <div class="abs phone">
    <svg width="11" height="11" viewBox="0 0 24 24"><path fill="#222" d="M6.6 10.8a15 15 0 0 0 6.6 6.6l2.2-2.2c.3-.3.7-.4 1-.2 1.1.4 2.3.6 3.6.6.6 0 1 .4 1 1V20c0 .6-.4 1-1 1A17 17 0 0 1 3 4c0-.6.4-1 1-1h3.5c.6 0 1 .4 1 1 0 1.3.2 2.5.6 3.6.1.3 0 .7-.2 1z"/></svg>
    085-3120744
  </div>
  <nav class="abs nav">
    <span class="active">HOME</span><span>OUR SOLUTIONS</span><span>OUR TEAM</span><span>JOB</span><span>CONTACT</span>
  </nav>
</header>

<section class="abs hero">
  <div class="hero-photo" role="img" aria-label="Photo of a team laughing together in a bright office"></div>
  <svg class="abs" style="left:0;top:0" width="671" height="246" viewBox="0 0 671 246">
    <path d="M0 0H238C308 22 352 92 338 142C326 192 294 230 271 246H0Z" fill="#ffffff"/>
    <path d="M0 0H232C300 20 345 90 333 140C322 190 290 230 265 246H0Z" fill="#1a9acb"/>
  </svg>
</section>
<h1 class="abs hero-title">We build mission<br>critical environments</h1>
<div class="abs hero-btn">CONTACT US</div>
<svg class="abs" style="left:21px;top:187px" width="10" height="16" viewBox="0 0 10 16"><path d="M8 2 2 8l6 6" fill="none" stroke="#fff" stroke-width="2.4"/></svg>
<svg class="abs" style="left:640px;top:187px" width="10" height="16" viewBox="0 0 10 16"><path d="m2 2 6 6-6 6" fill="none" stroke="#fff" stroke-width="2.4"/></svg>

<section>
  <h2 class="abs section-title about-title">About Us</h2>
  <p class="abs about-text">Aenean sed quam non sapien faucibus consequat vitae sit amet orci. Praesent quis risus mi. In mollis nulla in pulvinar dictum. Vivamus interdum sagittis felis, ut dapibus ligula feugiat ac. In dictum sapien eu tellus finibus fermentum. Aenean faucibus lacus ut mollis commodo. Donec vestibulum odio sem, ac laoreet massa ullamcorper id. Donec molestie nisi et tellus hendrerit vehicula. Nunc eu ligula sed quam pulvinar maximus in vitae eros. Proin porta fermentum ipsum, vel porttitor turpis venenatis luctus. Vivamus volutpat eu sapien quis tempus. Aenean feugiat viverra lorem ac sagittis.</p>
</section>

<section>
  <div class="abs wwd-photo" role="img" aria-label="Photo of colleagues working at computer screens in an office"></div>
  <h2 class="abs wwd-title">What We Do</h2>
  <div class="abs tile tile-green">
    <div class="tile-icon"><svg width="42" height="36" viewBox="0 0 42 36"><g fill="none" stroke="#fff" stroke-width="5" stroke-dasharray="3 2.3"><circle cx="13" cy="13" r="9"/><circle cx="31" cy="26" r="6"/></g><circle cx="13" cy="13" r="3.5" fill="#fff"/><circle cx="31" cy="26" r="2.3" fill="#fff"/></svg></div>
    Automation &amp;<br>Deployment
  </div>
  <div class="abs tile tile-teal">
    <div class="tile-icon"><svg width="40" height="38" viewBox="0 0 40 38"><rect x="3" y="16" width="18" height="20" fill="#fff"/><rect x="22" y="2" width="16" height="34" fill="#fff"/><circle cx="21.5" cy="24" r="3" fill="#11343f"/></svg></div>
    Mission Critical<br>Solutions
  </div>
  <div class="abs tile tile-slate">
    <div class="tile-icon"><svg width="56" height="38" viewBox="0 0 56 38"><path d="M12 36a10 10 0 0 1 0-20 16 16 0 0 1 30-4 12 12 0 0 1 2 24z" fill="#fff"/></svg></div>
    Cloud Consultancy
  </div>
  <div class="abs tile tile-blue">
    <div class="tile-icon"><svg width="42" height="38" viewBox="0 0 42 38"><circle cx="21" cy="7" r="6" fill="#fff"/><path d="M21 12v8M6 20h30M6 20v8M21 20v8M36 20v8" stroke="#fff" stroke-width="2.5" fill="none"/><rect x="1" y="28" width="10" height="8" fill="#fff"/><rect x="16" y="28" width="10" height="8" fill="#fff"/><rect x="31" y="28" width="10" height="8" fill="#fff"/></svg></div>
    Hyperconverged<br>Infrastructures
  </div>
  <div class="abs wwd-side"></div>
</section>

<section>
  <h2 class="abs section-title jobs-title">Jobs</h2>
  <article class="abs job-card" style="left:74px">
    <div class="job-date">18 APRIL, 2018</div>
    <p class="job-text">Nam et tortor in ante iaculis porttitor in luctus mi. Vivamus gravida sem a pretium euismod.</p>
    <div class="job-btn">Apply Now</div>
  </article>
  <article class="abs job-card" style="left:252px">
    <div class="job-date">18 APRIL, 2018</div>
    <p class="job-text">Nam et tortor in ante iaculis porttitor in luctus mi. Vivamus gravida sem a pretium euismod.</p>
    <div class="job-btn">Apply Now</div>
  </article>
  <article class="abs job-card" style="left:430px">
    <div class="job-date">18 APRIL, 2018</div>
    <p class="job-text">Nam et tortor in ante iaculis porttitor in luctus mi. Vivamus gravida sem a pretium euismod.</p>
    <div class="job-btn">Apply Now</div>
  </article>
  <div class="abs view-all"><span>VIEW ALL</span></div>
</section>

<section>
  <div class="abs partners"></div>
  <svg class="abs" style="left:0;top:1054px" width="190" height="81" viewBox="0 0 190 81">
    <path d="M0 0H148a40.5 40.5 0 0 1 0 81H0Z" fill="#fff"/>
    <path d="M0 0H144a40.5 40.5 0 0 1 0 81H0Z" fill="#11343f"/>
  </svg>
  <h2 class="abs partners-label">Partners</h2>
  <div class="abs partner" style="left:215px;width:58px;background:#c8c8c8"></div>
  <div class="abs partner" style="left:303px;width:62px;background:#2d5aa8"></div>
  <div class="abs partner" style="left:390px;width:145px;background:#bdbdbd"></div>
  <div class="abs partner" style="left:557px;width:40px;background:#7fb3cf"></div>
</section>

<footer>
  <div class="abs footer"></div>
  <div class="abs footer-links">Home &nbsp;|&nbsp; Our Solutions &nbsp;|&nbsp; Our Team &nbsp;|&nbsp; Job &nbsp;|&nbsp; Contact</div>
  <div class="abs footer-copy">Copyright © 2018 Orvane. All rights reserved.</div>
  <div class="abs social" style="left:435px;background:#3b5a98"></div>
  <div class="abs social" style="left:457px;background:#1d9ee6"></div>
  <div class="abs footer-address">Parklaan 12, 3511 AB Utrecht<br>085-3120744 &nbsp;|&nbsp; info@orvane.nl</div>
</footer>

</body>
</html>
```